New B2C website design to help dads be better dads

DadHarbor is a website to help dads be the “best dad you can be.”

We require our website to be designed into a PSD format, no coding necessary.

The general concept is a two-page design. The first page is the login page, the second page is the home page. Once at the home page, rather than navigating to and from different pages, the user will push and pull through different visual and functional layers of the hierarchy. In theory, this should add to the user experience by having a visual anchor of where they are (through layered pagination) as well as improving loading times since the new information should only be a delta in data load versus a brand new page load.

The general look-and-feel we are going for is clean, simple, minimal. This means that the winning design will show us a good eye for web-optimized typography, good use of white (negative) space, and good use of a visually pleasing grid.

We require a total of 6 page "views" plus the landing page. We note that many of the views are similar to one another.
Landing page
Milestone view
Task view
Content view, articles
Content view, products
Search view
What's new view

Please review all of the additional information provided as well as the attachments for examples.

We provide the following websites as good references for:

Typography:
http://example-kelvorn.com/journal/

Use of white space:
http://www.trenvaskit.com/
http://moldrefin.com/

Example for “scrolling” page concept as well as good balance of color, typography, and white space:
http://www.qorbitalmeet.eu/

Please contact us with questions so that we can guide your design effort.
Updates

Hello designers,

The following information is added to help guide the design process:

1.  For the text dialogue below the landing page, please assume the following word count:
"why are we making dad harbor?": 250 words
"who are we?" 200 words
"what's the deal with the penguin logo?" 300 words

For the social media links, please see http://www.gravelplumbs.com/
Notice the floating "social" bar that is always to the right.  This is the concept we are going for, please try to implement this as you see fit. 

Target Market(s)

Fathers of young children ages 0-6 years old.

Industry/Entity Type

Product

Font styles to use
Sans Serif

Requirements
Must have
• Clean lines, minimal design concept

Incorporation of our logo (see attached document)

Header content is static for all views after landing page, see example

This page WILL be responsive, please keep that in mind when designing
The timeline bar should be to the left, with the timeline bar’s “milestones” also being responsive.

Designer is free to suggest font types, but any fonts used must be royalty-free and web-optimized. We request a minimum number of font types as well as fonts that load relatively fast. We reinforce that visually appealing typography is a significant factor in the winning design choice.

While we are not expecting the winning design to include code, please keep in mind that the final implementation needs to be optimized for desktop, tablet, and mobile platforms.

If you are using stock photography that is not generated by you, please provide where/how we can obtain imagery, as well as price.

All custom graphics must be available in original formats; Photoshop/GIMP layered files for layout design, and vector formats for logos, icons and other graphical elements.

Please incorporate “Blue” into design elements as you see fit, as the RGB 67 74 169 Blue is the primary color used in our brand. The complement to this blue is 255 202 0, a brownish orange. Feel free to use this color as well, although please keep it to a lesser amount.

Background color is your choice, do not feel the need to use the grey.
Should not have
• Excessive graphical content such that it affects loading times

Excessive use of too many font types such that it affects loading times

```html
<!DOCTYPE html>
<html lang="en">
<head>
<meta charset="utf-8">
<title>DadHarbor – Home</title>
<link href="https://fonts.googleapis.com/css2?family=PT+Sans:wght@400;700&family=Roboto+Slab:wght@300;400&display=swap" rel="stylesheet">
<style>
:root{
  --brand-blue:#434aa9;
  --brand-gold:#ffca00;
  --welcome-gold:#dfa21f;
  --ink:#555;
  --ink-soft:#777;
  --ink-faint:#999;
  --rule:#d9d9d9;
  --page:#f7f7f7;
  --white:#fff;
  --card-border:#d6d6d6;
}
*{box-sizing:border-box;margin:0;padding:0}
html,body{width:891px;height:1200px;overflow:hidden}
body{position:relative;background:var(--page);font-family:"PT Sans",Arial,sans-serif;color:var(--ink)}
.site-header{position:absolute;left:0;top:0;width:891px;height:139px;background:var(--white);border-bottom:1px solid var(--rule)}
.brand{position:absolute;left:74px;top:56px;display:flex;align-items:center;gap:8px}
.brand-mark{width:22px;height:22px;border-radius:50%;background:var(--brand-blue)}
.brand-name{font-family:"PT Sans",sans-serif;font-weight:700;font-size:24px;color:var(--brand-blue)}
.welcome{position:absolute;right:74px;top:14px;font-family:"Roboto Slab",serif;font-weight:400;font-size:18.5px;color:var(--welcome-gold)}
.search{position:absolute;left:522px;top:58px;display:flex;gap:6px}
.search-input{width:227px;height:25px;border:1px solid #d4d4d4;font:11px "PT Sans",sans-serif;color:#999;padding:0 11px;line-height:23px}
.search-button{width:57px;height:25px;background:var(--brand-gold);border:1px solid #e6a900;font:700 11px "PT Sans",sans-serif;color:#8a5b00;text-align:center;line-height:23px}
.user-bar{position:absolute;left:522px;top:103px;font-size:11.5px;display:flex;align-items:center;white-space:nowrap}
.score{color:var(--brand-blue);display:flex;align-items:center;gap:6px}
.account-links{margin-left:30px;color:#888}
.account-links span{margin:0 6px;color:#bbb}
.timeline-rail{position:absolute;left:74px;top:157px;width:1px;height:1021px;background:var(--rule)}
.milestone{position:absolute;left:40px;display:flex;align-items:center}
.milestone-age{width:30px;font-size:9px;color:var(--ink-faint);text-align:right;margin-right:4px}
.milestone-dot{width:9px;height:9px;border-radius:50%;background:#555;display:flex;align-items:center;justify-content:center}
.milestone-dot::after{content:"";border-left:3px solid #fff;border-top:2px solid transparent;border-bottom:2px solid transparent;margin-left:1px}
.milestone-title{position:absolute;left:58px;white-space:nowrap;font-family:"Roboto Slab",serif;font-weight:300;color:#555}
.sort{position:absolute;left:674px;top:163px;display:flex;align-items:center;gap:8px;font-size:9.5px;color:#777}
.sort-select{width:102px;height:22px;background:var(--white);border:1px solid #ccc;color:#333;font-size:9.5px;padding:0 8px;line-height:20px;position:relative}
.sort-select::after{content:"";position:absolute;right:8px;top:9px;border-top:4px solid #555;border-left:3px solid transparent;border-right:3px solid transparent}
.section-rule{position:absolute;left:74px;top:211px;width:743px;height:1px;background:var(--rule)}
.task-list{position:absolute;left:98px;top:211px;width:180px;height:271px;background:var(--white);border:1px solid var(--rule);border-top:none;list-style:none;padding:0 7px}
.task{height:33px;border-bottom:1px solid #e6e6e6;display:flex;align-items:center;gap:8px;padding-left:12px;font-size:11px;color:#444}
.task:last-child{border-bottom:none}
.task-box{width:8px;height:8px;border:1px solid #aaa;background:#f3f3f3;position:relative}
.task.done .task-box::after{content:"";position:absolute;left:1px;top:0;width:3px;height:5px;border:solid #434aa9;border-width:0 1px 1px 0;transform:rotate(40deg)}
.intro{position:absolute;left:292px;width:522px;text-align:center;font-family:"Roboto Slab",serif}
.intro-title{top:231px;font-size:14px;color:#333}
.intro-sub{top:256px;font-size:10.5px;color:#555;font-weight:300}
.card{position:absolute;width:250px;height:280px;background:var(--white);border:1px solid var(--card-border)}
.card-media{position:absolute;left:4px;top:4px;width:241px;height:135px}
.card-badge{position:absolute;right:1px;bottom:1px;width:29px;height:31px;background:var(--brand-gold);display:flex;align-items:center;justify-content:center}
.card-title{position:absolute;left:12px;top:150px;width:225px;font-family:"Roboto Slab",serif;font-size:11.8px;line-height:17px;color:var(--brand-blue)}
.card-rating{position:absolute;left:13px;top:190px;display:flex;align-items:center;gap:9px;font-size:10.5px;color:#666}
.stars{display:flex;gap:1px}
.card-text{position:absolute;left:12px;top:208px;width:230px;font-size:10.2px;line-height:17px;color:#777}
.read-more{color:var(--brand-blue);white-space:nowrap}
.read-more svg{vertical-align:-1px;margin:0 2px 0 4px}
.social-bar{position:absolute;left:851px;top:521px;width:40px;height:159px;background:var(--brand-blue);border-radius:3px 0 0 3px;display:flex;flex-direction:column;align-items:center;justify-content:space-around;padding:8px 0}
.social-slot{width:16px;height:16px;border-radius:50%;border:2px solid var(--white)}
.footer-rule{position:absolute;left:0;top:1197px;width:891px;height:1px;background:var(--rule)}
</style>
</head>
<body>
<header class="site-header">
  <div class="brand"><span class="brand-mark"></span><span class="brand-name">DadHarbor</span></div>
  <p class="welcome">Welcome Greg, what would you like to do today?</p>
  <div class="search">
    <div class="search-input">Keyword...</div>
    <div class="search-button">SEARCH</div>
  </div>
  <div class="user-bar">
    <span class="score"><svg width="10" height="9" viewBox="0 0 10 9"><path d="M5 9 0.8 4.6A2.4 2.4 0 0 1 5 1.4 2.4 2.4 0 0 1 9.2 4.6Z" fill="#434aa9"/></svg>Super Dad Score: 10,500</span>
    <span class="account-links">My Account<span>|</span>Log out</span>
  </div>
</header>

<div class="timeline-rail"></div>

<div class="milestone" style="top:172px"><span class="milestone-age">-3 mo</span><span class="milestone-dot"></span><h1 class="milestone-title" style="font-size:18px;top:-11px">Prepare for the baby arrival</h1></div>
<div class="milestone" style="top:530px"><span class="milestone-age">0 mo</span><span class="milestone-dot"></span><h2 class="milestone-title" style="font-size:14.5px;top:-9px">What’s the Latest?</h2></div>
<div class="milestone" style="top:585px"><span class="milestone-age">0 mo</span><span class="milestone-dot"></span><h2 class="milestone-title" style="font-size:14.5px;top:-9px">What you searched for</h2></div>

<div class="sort">Sort by :<div class="sort-select">Most recent</div></div>
<div class="section-rule"></div>

<ul class="task-list">
  <li class="task"><span class="task-box"></span>Buy a crib</li>
  <li class="task"><span class="task-box"></span>Assemble the crib</li>
  <li class="task"><span class="task-box"></span>Buy a stroller</li>
  <li class="task done"><span class="task-box"></span>Buy a carseat</li>
  <li class="task"><span class="task-box"></span>Install a carseat</li>
  <li class="task"><span class="task-box"></span>Learn to change a diaper</li>
  <li class="task"><span class="task-box"></span>Learn to hold a baby</li>
  <li class="task"><span class="task-box"></span>Set a fedding schedule</li>
</ul>

<p class="intro intro-title">Your big day is almost here! Do you have your go-back packed?</p>
<p class="intro intro-sub">Do you have your routes (plural!) to the hospital mapped out? Lots to do, not much time!</p>

<svg width="0" height="0" style="position:absolute">
  <defs>
    <symbol id="star" viewBox="0 0 12 12"><path d="M6 .5 7.6 4.1 11.5 4.5 8.6 7.1 9.4 11 6 9 2.6 11 3.4 7.1.5 4.5 4.4 4.1Z" fill="#f7b500"/></symbol>
    <symbol id="star-half" viewBox="0 0 12 12"><path d="M6 .5 7.6 4.1 11.5 4.5 8.6 7.1 9.4 11 6 9 2.6 11 3.4 7.1.5 4.5 4.4 4.1Z" fill="none" stroke="#f7b500" stroke-width=".9"/><path d="M6 .5V9L2.6 11 3.4 7.1.5 4.5 4.4 4.1Z" fill="#f7b500"/></symbol>
    <symbol id="doc" viewBox="0 0 16 20"><path d="M4 0h12v16H4z" fill="#222"/><path d="M0 3h11v17H0z" fill="#111" stroke="#ffca00" stroke-width="1"/></symbol>
    <symbol id="cart" viewBox="0 0 22 18"><path d="M0 1.5h4l3 10h11l3-7H5.5" fill="none" stroke="#222" stroke-width="2"/><path d="M8 6.5h11M8.5 9h9.5" stroke="#222" stroke-width="1.2"/><circle cx="8.5" cy="15.5" r="1.8" fill="#222"/><circle cx="16.5" cy="15.5" r="1.8" fill="#222"/></symbol>
    <symbol id="plus" viewBox="0 0 10 10"><circle cx="5" cy="5" r="5" fill="#434aa9"/><path d="M5 2.5v5M2.5 5h5" stroke="#fff" stroke-width="1.4"/></symbol>
  </defs>
</svg>

<article class="card" style="left:292px;top:294px">
  <div class="card-media" role="img" aria-label="Photo of a baby playing with toys in a rear-facing car seat" style="background:linear-gradient(135deg,#3a3d44,#7d8088 55%,#2f3034)"></div>
  <div class="card-media" style="background:none"><span class="card-badge"><svg width="15" height="19"><use href="#doc"/></svg></span></div>
  <h3 class="card-title">Pellentesque habitant morbi tristique senectus et netus</h3>
  <div class="card-rating"><span class="stars"><svg width="13" height="13"><use href="#star"/></svg><svg width="13" height="13"><use href="#star"/></svg><svg width="13" height="13"><use href="#star"/></svg><svg width="13" height="13"><use href="#star"/></svg><svg width="13" height="13"><use href="#star-half"/></svg></span>3,121 ratings</div>
  <p class="card-text">I went out to buy my first car seat and had to earn my PhD in car seats, Newtonian physics, and anti-stain technology···<span class="read-more"><svg width="10" height="10"><use href="#plus"/></svg>Read More</span></p>
</article>

<article class="card" style="left:564px;top:294px">
  <div class="card-media" role="img" aria-label="Photo of a smiling baby in an infant car seat" style="background:linear-gradient(135deg,#8a7c68,#b8a58a 50%,#5a4e40)"></div>
  <div class="card-media" style="background:none"><span class="card-badge"><svg width="22" height="18"><use href="#cart"/></svg></span></div>
  <h3 class="card-title">Pellentesque habitant morbi tristique senectus et netus</h3>
  <div class="card-rating"><span class="stars"><svg width="13" height="13"><use href="#star"/></svg><svg width="13" height="13"><use href="#star"/></svg><svg width="13" height="13"><use href="#star"/></svg><svg width="13" height="13"><use href="#star"/></svg><svg width="13" height="13"><use href="#star-half"/></svg></span>3,121 ratings</div>
  <p class="card-text">I went out to buy my first car seat and had to earn my PhD in car seats, Newtonian physics, and anti-stain technology···<span class="read-more"><svg width="10" height="10"><use href="#plus"/></svg>Read More</span></p>
</article>

<article class="card" style="left:292px;top:597px">
  <div class="card-media" role="img" aria-label="Photo of a laughing toddler in a red car seat" style="background:linear-gradient(135deg,#7a4a30,#c89870 50%,#a82a20)"></div>
  <div class="card-media" style="background:none"><span class="card-badge"><svg width="15" height="19"><use href="#doc"/></svg></span></div>
  <h3 class="card-title">Pellentesque habitant morbi tristique senectus et netus</h3>
  <div class="card-rating"><span class="stars"><svg width="13" height="13"><use href="#star"/></svg><svg width="13" height="13"><use href="#star"/></svg><svg width="13" height="13"><use href="#star"/></svg><svg width="13" height="13"><use href="#star"/></svg><svg width="13" height="13"><use href="#star-half"/></svg></span>3,121 ratings</div>
  <p class="card-text">I went out to buy my first car seat and had to earn my PhD in car seats, Newtonian physics, and anti-stain technology···<span class="read-more"><svg width="10" height="10"><use href="#plus"/></svg>Read More</span></p>
</article>

<article class="card" style="left:564px;top:597px">
  <div class="card-media" role="img" aria-label="Photo of a baby buckled into a grey and orange infant seat" style="background:linear-gradient(135deg,#3e4046,#6a6c72 50%,#3a3b40)"></div>
  <div class="card-media" style="background:none"><span class="card-badge"><svg width="22" height="18"><use href="#cart"/></svg></span></div>
  <h3 class="card-title">Pellentesque habitant morbi tristique senectus et netus</h3>
  <div class="card-rating"><span class="stars"><svg width="13" height="13"><use href="#star"/></svg><svg width="13" height="13"><use href="#star"/></svg><svg width="13" height="13"><use href="#star"/></svg><svg width="13" height="13"><use href="#star"/></svg><svg width="13" height="13"><use href="#star-half"/></svg></span>3,121 ratings</div>
  <p class="card-text">I went out to buy my first car seat and had to earn my PhD in car seats, Newtonian physics, and anti-stain technology···<span class="read-more"><svg width="10" height="10"><use href="#plus"/></svg>Read More</span></p>
</article>

<article class="card" style="left:292px;top:900px">
  <div class="card-media" role="img" aria-label="Photo of a baby held by a vehicle seat belt" style="background:linear-gradient(135deg,#5f7a7e,#a9b8b4 50%,#707a78)"></div>
  <div class="card-media" style="background:none"><span class="card-badge"><svg width="15" height="19"><use href="#doc"/></svg></span></div>
  <h3 class="card-title">Pellentesque habitant morbi tristique senectus et netus</h3>
  <div class="card-rating"><span class="stars"><svg width="13" height="13"><use href="#star"/></svg><svg width="13" height="13"><use href="#star"/></svg><svg width="13" height="13"><use href="#star"/></svg><svg width="13" height="13"><use href="#star"/></svg><svg width="13" height="13"><use href="#star-half"/></svg></span>3,121 ratings</div>
  <p class="card-text">I went out to buy my first car seat and had to earn my PhD in car seats, Newtonian physics, and anti-stain technology···<span class="read-more"><svg width="10" height="10"><use href="#plus"/></svg>Read More</span></p>
</article>

<article class="card" style="left:564px;top:900px">
  <div class="card-media" role="img" aria-label="Photo of a sleeping newborn in a brown car seat" style="background:linear-gradient(135deg,#3a2c24,#b89a88 50%,#5a463a)"></div>
  <div class="card-media" style="background:none"><span class="card-badge"><svg width="22" height="18"><use href="#cart"/></svg></span></div>
  <h3 class="card-title">Pellentesque habitant morbi tristique senectus et netus</h3>
  <div class="card-rating"><span class="stars"><svg width="13" height="13"><use href="#star"/></svg><svg width="13" height="13"><use href="#star"/></svg><svg width="13" height="13"><use href="#star"/></svg><svg width="13" height="13"><use href="#star"/></svg><svg width="13" height="13"><use href="#star-half"/></svg></span>3,121 ratings</div>
  <p class="card-text">I went out to buy my first car seat and had to earn my PhD in car seats, Newtonian physics, and anti-stain technology···<span class="read-more"><svg width="10" height="10"><use href="#plus"/></svg>Read More</span></p>
</article>

<nav class="social-bar" aria-label="Share">
  <span class="social-slot"></span>
  <span class="social-slot"></span>
  <span class="social-slot"></span>
  <span class="social-slot"></span>
</nav>

<div class="footer-rule"></div>
</body>
</html>
```